card for handyman and landscaping business, double sided with services listed on the back

Design a business card for a handyman and Landscaping business in San Jose,ca. Would like front to be a house with 3D characters doing different tasks i.e. Mowing lawn, painting, sprinklers, lighting, weed whacking, power washing, lumber etc. on the backside a cutout of the interior with computer, internet, cleaning, bathroom/kitchen remodeling, smart home etc.

Industry/Entity Type

Handyman

Contact Information for Business Card

Two sided view of a house, one outside services and one inside services

Colors

Designer to choose colors to be used in the design.

Requirements
Must have
• General Household Repairs and Maintenance
• Landscaping, Gardening, and Planting
• Painting, Patching and Trim/Moulding Work
• Cleaning, Restoring and Hauling/Trash Removal
• Blinds, Curtains, and Assembly Work
• Computer, Internet/Wireless, and Smart Home Service

```html
<!DOCTYPE html>
<html lang="en">
<head>
<meta charset="utf-8">
<title>Handyman Landscaping and Tech Services – Business Card</title>
<link rel="stylesheet" href="https://fonts.googleapis.com/css2?family=Montserrat:wght@600;700&family=Lato:wght@400;700&display=swap">
<style>
  :root{
    --backdrop:#4d4d4d;
    --green-light:#2f9e4f;
    --green-dark:#0b4c2b;
    --paper:#f0f0f0;
    --white:#ffffff;
  }
  *{margin:0;padding:0;box-sizing:border-box}
  html,body{width:1200px;height:900px;overflow:hidden;background:var(--backdrop)}
  .stage{position:relative;width:1200px;height:900px}
  .card{position:absolute;top:306px;width:437px;height:271px;overflow:hidden;
        box-shadow:2px 3px 6px rgba(0,0,0,.45)}
  .card--front{left:150px}
  .card--back{left:611px}
  .card__art{position:absolute;inset:0;width:437px;height:271px}
  .card__title{position:absolute;top:0;left:0;right:0;height:49px;display:flex;align-items:center;
        font-family:"Montserrat",sans-serif;font-weight:700;color:var(--white);font-size:15.5px;letter-spacing:.1px}
  .card--front .card__title{padding-left:20px}
  .card--back .card__title{justify-content:center;font-size:16px;padding-bottom:2px}
  .contact{position:absolute;left:28px;top:78px;font-family:"Lato",sans-serif;color:var(--white);font-size:12px;line-height:16px}
  .contact__row{display:flex;align-items:center;gap:6px}
  .contact__row svg{width:9px;height:9px;fill:var(--white)}
  .contact__address{margin-top:10px;font-size:12px;line-height:16px}
  .person{position:absolute;right:27px;top:76px;text-align:right;font-family:"Lato",sans-serif;color:var(--white)}
  .person__name{font-family:"Montserrat",sans-serif;font-weight:700;font-size:14.5px;line-height:18px}
  .person__role{font-size:12px;line-height:14px}
  .services{position:absolute;top:60px;list-style:none;font-family:"Lato",sans-serif;color:var(--white);font-size:11px;line-height:13.9px}
  .services li{position:relative}
  .services--left{left:19px}
  .services--left li{padding-left:11px}
  .services--left li::before{content:"";position:absolute;left:0;top:5px;width:4px;height:4px;border-radius:50%;background:var(--white)}
  .services--right{right:26px;text-align:right}
  .services--right li{padding-right:10px}
  .services--right li::after{content:"";position:absolute;right:0;top:5px;width:4px;height:4px;border-radius:50%;background:var(--white)}
</style>
</head>
<body>
<div class="stage">

  <section class="card card--front">
    <svg class="card__art" viewBox="0 0 437 271" aria-hidden="true">
      <rect x="0" y="0" width="437" height="271" fill="var(--paper)"/>
      <rect x="0" y="0" width="437" height="49" fill="var(--green-light)"/>
      <rect x="0" y="49" width="437" height="137" fill="var(--green-dark)"/>
      <polygon points="197,186 197,152 256,131 311,152 311,186" fill="var(--paper)"/>
      <polyline points="0,184 197,184 197,152 256,131 311,152 311,184 437,184" fill="none" stroke="var(--green-light)" stroke-width="3"/>
      <g fill="var(--green-light)">
        <circle cx="55" cy="229" r="25"/><circle cx="120" cy="229" r="25"/><circle cx="186" cy="229" r="25"/>
        <circle cx="251" cy="229" r="25"/><circle cx="316" cy="229" r="25"/><circle cx="383" cy="229" r="25"/>
      </g>
      <g fill="var(--white)" stroke="none">
        <!-- toilet -->
        <rect x="45" y="213" width="20" height="12" rx="2"/>
        <path d="M44 227h22c0 7-4 10-8 11v5h-6v-5c-4-1-8-4-8-11z"/>
        <!-- broom -->
        <path d="M128 213l2 1-8 14-2-1z"/>
        <path d="M117 226l7 4c-2 5-6 9-12 9 1-5 2-10 5-13z"/>
        <!-- router -->
        <rect x="175" y="218" width="22" height="18" rx="2"/>
        <rect x="178" y="238" width="16" height="3" rx="1"/>
      </g>
      <g fill="none" stroke="var(--green-light)" stroke-width="1.5">
        <path d="M181 227a7 7 0 0 1 10 0M183 230a4 4 0 0 1 6 0"/>
      </g>
      <g fill="none" stroke="var(--white)" stroke-width="2" stroke-linecap="round">
        <!-- antenna -->
        <path d="M251 226v16M245 242h12"/>
        <path d="M245 221a8 8 0 0 0 0 12M257 221a8 8 0 0 1 0 12M240 217a14 14 0 0 0 0 20M262 217a14 14 0 0 1 0 20"/>
        <!-- bulb rays -->
        <path d="M316 210v3M305 215l2 2M327 215l-2 2M302 226h3M330 226h-3"/>
        <!-- smart home -->
        <path d="M372 230l11-10 11 10M375 228v13h16v-13"/>
        <path d="M383 227v4M379 229a5 5 0 1 0 8 0"/>
      </g>
      <g fill="var(--white)">
        <circle cx="251" cy="227" r="2.5"/>
        <circle cx="316" cy="226" r="8"/>
        <rect x="312" y="233" width="8" height="6" rx="1"/>
      </g>
    </svg>
    <h1 class="card__title">HANDYMAN&nbsp; LANDSCAPING AND TECH SERVICES</h1>
    <div class="contact">
      <div class="contact__row"><svg viewBox="0 0 10 10"><path d="M2 0l2 2-1 2c1 1 2 2 3 3l2-1 2 2-1 2C4 10 0 6 0 1z"/></svg>044 987654321</div>
      <div class="contact__row"><svg viewBox="0 0 10 10"><path d="M0 2h10v6H0zM0 2l5 3 5-3" /></svg>hello@hollyoakfix.com</div>
      <div class="contact__row"><svg viewBox="0 0 10 10"><circle cx="5" cy="5" r="5"/></svg>www.hollyoakfix.com</div>
      <p class="contact__address">5678, Orchard Lane,<br>Country name, 54321</p>
    </div>
    <div class="person">
      <p class="person__name">MARCUS HALE</p>
      <p class="person__role">Managing Director</p>
    </div>
  </section>

  <section class="card card--back">
    <svg class="card__art" viewBox="0 0 437 271" aria-hidden="true">
      <rect x="0" y="0" width="437" height="271" fill="var(--paper)"/>
      <rect x="0" y="0" width="437" height="49" fill="var(--green-light)"/>
      <rect x="0" y="49" width="437" height="137" fill="var(--green-dark)"/>
      <polygon points="124,186 124,153 182,131 241,153 241,186" fill="var(--paper)"/>
      <polyline points="0,184 124,184 124,153 182,131 241,153 241,184 437,184" fill="none" stroke="var(--green-light)" stroke-width="3"/>
      <g fill="var(--green-light)">
        <circle cx="53" cy="229" r="25"/><circle cx="118" cy="229" r="25"/><circle cx="184" cy="229" r="25"/>
        <circle cx="250" cy="229" r="25"/><circle cx="316" cy="229" r="25"/><circle cx="382" cy="229" r="25"/>
      </g>
      <g fill="var(--white)">
        <!-- mower -->
        <path d="M31 216l2-1 10 14h20v8H41z"/>
        <circle cx="47" cy="238" r="3"/><circle cx="63" cy="238" r="3"/>
        <!-- trowel -->
        <path d="M104 214l4-2 10 12-3 3z"/>
        <path d="M112 227l18 4-2 6-18-5z"/>
        <!-- paint roller -->
        <rect x="175" y="213" width="18" height="8" rx="2"/>
        <path d="M193 216h3v9h-11v4h-2v-6h11z"/>
        <rect x="182" y="229" width="4" height="13" rx="1"/>
        <!-- pressure washer -->
        <path d="M237 224h20v4h-14v8h-4v-8h-2z"/>
        <path d="M258 222l8-3v10l-8-3z"/>
        <!-- bin -->
        <rect x="305" y="216" width="22" height="3" rx="1"/>
        <path d="M307 220h18l-2 20h-14z"/>
        <!-- window -->
        <rect x="370" y="217" width="24" height="24"/>
      </g>
      <g fill="var(--green-light)">
        <circle cx="309" cy="241" r="2.5"/>
        <rect x="373" y="220" width="8" height="8"/><rect x="383" y="220" width="8" height="8"/>
        <rect x="373" y="230" width="8" height="8"/><rect x="383" y="230" width="8" height="8"/>
      </g>
    </svg>
    <h2 class="card__title">SERVICES</h2>
    <ul class="services services--left">
      <li>Handyman</li><li>Landscaping</li><li>Sprinklers/Irrigation</li><li>Painting</li>
      <li>Electrical</li><li>Lighting</li><li>Power Washing</li><li>Hauling</li>
    </ul>
    <ul class="services services--right">
      <li>Cleaning</li><li>Bath/Kitchen</li><li>Baseboards/Trim/Moulding</li><li>Smart Home</li>
      <li>A/C and Heating</li><li>Blinds, Curtains</li><li>Assembly Services</li><li>Computer/Tech Service</li>
    </ul>
  </section>

</div>
</body>
</html>
```